Larkspur Talent IT Recruiting firm needs a business card design for Recruiters, Sourcers, and Account

We need business cards that allow us to change all contact info, names, titles (Recruiter, Sourcer, Account Manager, Director, CEO, etc) per person since we have three offices, in three cities, Phoenix, Austin, and Las Vegas. We do recruiting and contractors for IT positions (Developers, Architects, Software Engineers, Security Engineers, Help Desk, DBAs, PMs, Scrum Masters, etc.) Our client companies are very diverse from Meridian 100 to silicone Valley type start-ups.

So, while we what hip, techie, and quirky, it still needs to be professional. Primary color we use is blue, with silver as a secondary color.

Target Market(s)

IT, Technology

Industry/Entity Type

Business

Contact Information for Business Card

Company name: Larkspur Talent, Inc.
Website: www.larkspurtalent.example
Logos for Careerloop, Blipster, and Myriada

Name, Title, Office Number, Cell Number, email

Font styles to use
Serif
Sans Serif

Colors
0455a3
d5d5d5

Requirements
Nice to have
• The grey I selected below is not necessary - but, would like silver included. I included a card design (File 3: LTI early trial example.jpg) that I had started on. It's very rough, and not quite what we're looking for, but what we did like is the logo, big, maybe a bit faded, off center, goes out of frame, etc. Still looking for other ideas - you are the pros! But, just an idea of a design element we liked.

```html
<!DOCTYPE html>
<html lang="en">
<head>
<meta charset="utf-8">
<title>Larkspur Talent — Business Card</title>
<link rel="stylesheet" href="https://fonts.googleapis.com/css2?family=Open+Sans:wght@400;600;700&family=Cormorant+Garamond:wght@500&display=swap">
<style>
  :root {
    --brand-blue: #0455a3;
    --bright-blue: #1a86d0;
    --pale-blue: #c9dcef;
    --silver: #d5d5d5;
    --silver-dark: #a9a9a9;
    --ink: #1c1c1c;
    --paper: #ffffff;
    --backdrop: #eceef1;
  }
  html, body {
    margin: 0;
    padding: 0;
    width: 1200px;
    height: 1020px;
    overflow: hidden;
    background: var(--backdrop);
    font-family: "Open Sans", Arial, sans-serif;
  }
  .canvas {
    position: relative;
    width: 1200px;
    height: 1020px;
  }
  .card {
    position: absolute;
    left: 75px;
    top: 210px;
    width: 1050px;
    height: 600px;
    background: var(--paper);
    box-shadow: 0 12px 34px rgba(0,0,0,0.18);
    overflow: hidden;
  }
  .card-art {
    position: absolute;
    inset: 0;
  }
  .holder {
    position: absolute;
    left: 52px;
    top: 300px;
    color: var(--paper);
  }
  .holder-name {
    font-weight: 700;
    font-size: 36px;
    letter-spacing: 0.5px;
    margin: 0;
    line-height: 1.1;
  }
  .holder-title {
    font-weight: 400;
    font-size: 22px;
    letter-spacing: 0.6px;
    margin: 4px 0 0;
  }
  .brand {
    position: absolute;
    left: 585px;
    top: 190px;
    text-align: left;
  }
  .brand-row {
    display: flex;
    align-items: center;
    gap: 12px;
  }
  .brand-dot {
    width: 38px;
    height: 38px;
    border-radius: 50%;
    background: var(--bright-blue);
  }
  .brand-name {
    font-weight: 600;
    font-size: 34px;
    letter-spacing: 3px;
    color: var(--ink);
  }
  .brand-tagline {
    font-family: "Cormorant Garamond", Georgia, serif;
    font-weight: 500;
    font-size: 15px;
    letter-spacing: 3.5px;
    color: var(--ink);
    margin: 10px 0 0 52px;
  }
  .contacts {
    position: absolute;
    left: 40px;
    top: 474px;
    margin: 0;
    padding: 0;
    list-style: none;
  }
  .contact {
    display: flex;
    align-items: center;
    gap: 16px;
    height: 29px;
    font-size: 16px;
    color: var(--ink);
  }
  .contact-icon {
    width: 30px;
    height: 20px;
    flex: none;
  }
</style>
</head>
<body>
<main class="canvas">
  <article class="card">
    <svg class="card-art" width="1050" height="600" viewBox="0 0 1050 600" aria-hidden="true">
      <defs>
        <radialGradient id="blueField" cx="0.45" cy="0.35" r="0.75">
          <stop offset="0" stop-color="#1c8fd8"/>
          <stop offset="1" stop-color="#0455a3"/>
        </radialGradient>
        <linearGradient id="paleSwoosh" x1="0" y1="0" x2="1" y2="0">
          <stop offset="0" stop-color="#b8d0ea"/>
          <stop offset="1" stop-color="#ffffff"/>
        </linearGradient>
        <linearGradient id="silverSweep" x1="1" y1="0" x2="0" y2="0.3">
          <stop offset="0" stop-color="#9c9c9c"/>
          <stop offset="0.55" stop-color="#d5d5d5"/>
          <stop offset="1" stop-color="#f7f7f7"/>
        </linearGradient>
      </defs>
      <path class="silver-sweep" d="M870 0 H1050 V600 H1030 C990 400 960 170 870 0 Z" fill="url(#silverSweep)"/>
      <path class="pale-swoosh" d="M0 452 C390 430 500 380 522 260 C540 150 580 60 690 0 H720 C610 70 570 170 552 280 C530 410 420 470 0 480 Z" fill="url(#paleSwoosh)"/>
      <path class="ink-line" d="M0 446 C385 424 488 372 508 258 C528 145 570 50 676 0" fill="none" stroke="#151515" stroke-width="9"/>
      <path class="blue-field" d="M0 0 H660 C560 48 518 140 498 252 C478 362 380 414 0 436 Z" fill="url(#blueField)"/>
    </svg>

    <div class="holder">
      <h1 class="holder-name">DORIAN WELLS</h1>
      <p class="holder-title">GENERAL MANAGER</p>
    </div>

    <div class="brand">
      <div class="brand-row">
        <span class="brand-dot"></span>
        <span class="brand-name">LARKSPUR TALENT</span>
      </div>
      <p class="brand-tagline">BUILDING TEAMS THAT LAST</p>
    </div>

    <ul class="contacts">
      <li class="contact">
        <svg class="contact-icon" viewBox="0 0 30 20" aria-hidden="true">
          <rect width="30" height="20" fill="#151515"/><rect y="16" width="30" height="4" fill="#0455a3"/>
          <path d="M12 4 l2 0 l1 3 l-1.5 1 a6 6 0 0 0 3 3 l1-1.5 l3 1 l0 2 a2 2 0 0 1-2 1.5 a9 9 0 0 1-8.5-8.5 a2 2 0 0 1 2-1.5z" fill="#fff" transform="translate(-1,-1) scale(0.95)"/>
        </svg>
        <span>012 555 0148</span>
      </li>
      <li class="contact">
        <svg class="contact-icon" viewBox="0 0 30 20" aria-hidden="true">
          <rect width="30" height="20" fill="#151515"/><rect y="16" width="30" height="4" fill="#0455a3"/>
          <rect x="9" y="4" width="12" height="9" fill="none" stroke="#fff" stroke-width="1.4"/>
          <path d="M9 4 l6 5 l6-5" fill="none" stroke="#fff" stroke-width="1.4"/>
        </svg>
        <span>dwells@larkspurtalent.example</span>
      </li>
      <li class="contact">
        <svg class="contact-icon" viewBox="0 0 30 20" aria-hidden="true">
          <rect width="30" height="20" fill="#151515"/><rect y="16" width="30" height="4" fill="#0455a3"/>
          <circle cx="15" cy="8.5" r="5.5" fill="none" stroke="#fff" stroke-width="1.3"/>
          <ellipse cx="15" cy="8.5" rx="2.3" ry="5.5" fill="none" stroke="#fff" stroke-width="1.1"/>
          <line x1="9.5" y1="8.5" x2="20.5" y2="8.5" stroke="#fff" stroke-width="1.1"/>
        </svg>
        <span>www.larkspurtalent.example</span>
      </li>
      <li class="contact">
        <svg class="contact-icon" viewBox="0 0 30 20" aria-hidden="true">
          <rect width="30" height="20" fill="#151515"/><rect y="16" width="30" height="4" fill="#0455a3"/>
          <path d="M15 14 C12 10 11 8.5 11 7 a4 4 0 0 1 8 0 c0 1.5-1 3-4 7z" fill="#fff"/>
          <circle cx="15" cy="7" r="1.5" fill="#151515"/>
        </svg>
        <span>Suite 410, Cedar Bend Avenue, Tempe</span>
      </li>
    </ul>
  </article>
</main>
</body>
</html>
```